Real Estate Flyer

Hi - I am assisting a relative to sell a unit. I am looking to have a two page flyer designed (configured as a single page with back to back printing). I have uploaded two samples to give you an idea of the look and feel - one which relates to this property when originally purchased, the other for a different property.
The flyer should includes several key photos on the front along with the wording. The rear should include any secondary photos along with the floor plan.
The flyer should be close to A4 size.

Updates
Hi,
Industry/Entity Type
Real Estate
Look and feel
Each slider illustrates characteristics of the customer's brand and the style your logo design should communicate.

```html
<!DOCTYPE html>
<html lang="en">
<head>
<meta charset="utf-8">
<title>Oversized apartment in a lifestyle location</title>
<link rel="stylesheet" href="https://fonts.googleapis.com/css2?family=Ubuntu:wght@300;400;500;700&display=swap">
<style>
  :root {
    --bg-top: #050505;
    --bg-bottom: #2b2b2b;
    --text: #ffffff;
    --text-soft: #e6e6e6;
    --tick: #8cc63f;
    --photo-terrace: linear-gradient(135deg, #c79a6e 0%, #b36a48 45%, #d9c3a3 70%, #3a86d6 100%);
    --photo-kitchen: linear-gradient(135deg, #f2efe8 0%, #dcd7cc 60%, #8a7a6a 100%);
    --photo-bath: linear-gradient(135deg, #f5f5f2 0%, #dfe3e4 60%, #9aa6ad 100%);
  }
  * { margin: 0; padding: 0; box-sizing: border-box; }
  html, body { width: 849px; height: 1200px; overflow: hidden; background: #000; }
  .flyer {
    position: relative; width: 849px; height: 1200px; overflow: hidden;
    background: linear-gradient(180deg, var(--bg-top) 0%, #1a1a1a 50%, var(--bg-bottom) 100%);
    font-family: "Ubuntu", sans-serif; color: var(--text);
  }
  .headline {
    position: absolute; left: 47px; top: 48px; width: 750px;
    font-size: 40px; font-weight: 500; letter-spacing: -0.8px; white-space: nowrap;
  }
  .specs {
    position: absolute; right: 53px; top: 105px;
    font-size: 19px; font-weight: 400; letter-spacing: -0.3px;
  }
  .photo { position: absolute; }
  .photo-hero { left: 50px; top: 152px; width: 756px; height: 346px; background: var(--photo-terrace); }
  .photo-kitchen { left: 49px; top: 520px; width: 240px; height: 170px; background: var(--photo-kitchen); }
  .photo-terrace { left: 307px; top: 520px; width: 240px; height: 170px; background: var(--photo-terrace); }
  .photo-bath { left: 565px; top: 520px; width: 240px; height: 170px; background: var(--photo-bath); }
  .inspect {
    position: absolute; top: 698px; left: 0; width: 849px; font-size: 28px; font-weight: 300;
    color: var(--text-soft); letter-spacing: -0.5px;
  }
  .inspect span { position: absolute; white-space: nowrap; }
  .address {
    position: absolute; top: 767px; left: 0; width: 849px; text-align: center;
    font-size: 23px; font-weight: 500; letter-spacing: -0.3px;
  }
  .intro {
    position: absolute; left: 49px; top: 814px; width: 760px;
    font-size: 15px; line-height: 19.5px; font-weight: 300; letter-spacing: -0.3px;
  }
  .features { position: absolute; list-style: none; font-size: 15px; font-weight: 300; letter-spacing: -0.3px; }
  .features li { position: absolute; padding-left: 18px; white-space: nowrap; line-height: 19.5px; }
  .features svg { position: absolute; left: 0; top: 4px; }
  .features-left { left: 64px; top: 925px; }
  .features-right { left: 453px; top: 925px; }
  .rates { position: absolute; left: 48px; top: 1050px; font-size: 15px; font-weight: 300; line-height: 19.5px; letter-spacing: -0.3px; }
  .rates div { position: relative; height: 19.5px; white-space: nowrap; }
  .rates .value { position: absolute; left: 122px; top: 0; }
  .contact { position: absolute; left: 532px; top: 1050px; width: 264px; text-align: center; font-weight: 300; }
  .contact-name { font-size: 27px; letter-spacing: -0.5px; white-space: nowrap; }
  .contact-name .label { margin-right: 22px; }
  .contact-note { font-size: 17px; margin-top: 2px; letter-spacing: -0.3px; }
  .contact-phone { font-size: 27px; font-weight: 400; margin-top: 6px; }
</style>
</head>
<body>
<main class="flyer">
  <h1 class="headline">Oversized apartment in a lifestyle location</h1>
  <p class="specs">2 BED | 1 BATH | 1 CAR</p>

  <div class="photo photo-hero" role="img" aria-label="Living room opening onto a curved terrace with brick building and sky view"></div>
  <div class="photo photo-kitchen" role="img" aria-label="White kitchen with wall oven and window"></div>
  <div class="photo photo-terrace" role="img" aria-label="Curved terrace outside the living area"></div>
  <div class="photo photo-bath" role="img" aria-label="Tiled bathroom with shower, vanity and mirror"></div>

  <div class="inspect">
    <span style="left:145px">Inspect :</span>
    <span style="left:284px">Sat 10:45 – 11:30</span>
    <span style="left:533px">Wed 12:00 – 12:30</span>
  </div>

  <h2 class="address">12/40-46 Wattle Lane, ELM JUNCTION</h2>

  <p class="intro">Peacefully positioned on the 5th floor of a refurbished security building, this superbly spacious residence combines modern, low maintenance apartment living with inviting prospects for the entertainer. Boasting a huge full-width terrace on-title, its sought-after setting in the heart of Elm Junction offers the ultimate in lifestyle and convenience.</p>

  <ul class="features features-left">
    <li style="top:0"><svg width="16" height="14" viewBox="0 0 16 14"><path d="M1 7 L6 12 L15 1" fill="none" stroke="var(--tick)" stroke-width="2.2" stroke-linecap="round"/></svg>Expansive open plan living and dining area</li>
    <li style="top:36px"><svg width="16" height="14" viewBox="0 0 16 14"><path d="M1 7 L6 12 L15 1" fill="none" stroke="var(--tick)" stroke-width="2.2" stroke-linecap="round"/></svg>Terrace features city and Marlow Bay glimpses</li>
    <li style="top:73px"><svg width="16" height="14" viewBox="0 0 16 14"><path d="M1 7 L6 12 L15 1" fill="none" stroke="var(--tick)" stroke-width="2.2" stroke-linecap="round"/></svg>Kitchen updated with Corvel gas appliances</li>
  </ul>
  <ul class="features features-right">
    <li style="top:0"><svg width="16" height="14" viewBox="0 0 16 14"><path d="M1 7 L6 12 L15 1" fill="none" stroke="var(--tick)" stroke-width="2.2" stroke-linecap="round"/></svg>Built-ins in both bedrooms, fully tiled bathrooms</li>
    <li style="top:36px"><svg width="16" height="14" viewBox="0 0 16 14"><path d="M1 7 L6 12 L15 1" fill="none" stroke="var(--tick)" stroke-width="2.2" stroke-linecap="round"/></svg>Internal laundry, secure parking, lift, outdoor<br>pool and gymnasium</li>
    <li style="top:92px"><svg width="16" height="14" viewBox="0 0 16 14"><path d="M1 7 L6 12 L15 1" fill="none" stroke="var(--tick)" stroke-width="2.2" stroke-linecap="round"/></svg>Steps to station, Harbourside Mall and Greenfield Park</li>
  </ul>

  <div class="rates">
    <div>Water Rates:<span class="value">To be provided on finalizing design</span></div>
    <div>Council Rates:<span class="value" style="left:139px">To be provided on finalizing design</span></div>
    <div>Strata Rates:<span class="value">To be provided on finalizing design</span></div>
    <div>Estimated</div>
    <div>Market Rental:<span class="value" style="left:120px">$700.00 p/w</span></div>
  </div>

  <div class="contact">
    <p class="contact-name"><span class="label">Contact:</span>Dean Harlow</p>
    <p class="contact-note">(Assisting owner in Private Sale)</p>
    <p class="contact-phone">0400 555 187</p>
  </div>
</main>
</body>
</html>
```